World Cup Banner 3 Feet by 8 Feet

It seems like the photos i submitted are bad quality. Feel free to find some of your own with better resolution. I am not super picky on what is uses as I think I've conveyed my concept and most of you understand.
FEEL FREE TO GET CREATIVE AND ADD PICS OF UR OWN IF U WANT
I am going to Brazil for world cup as a Fan of Mexico National Soccer team. I need a super bad ass banner design. I am not picky and I am attaching several images that you are free to play with. Requirements are as follow:
1. The two pictures of the saints would be ideal. Blend them in so they dont look like like square images.
2. On the bottom at smaller scale so it doesnt take much space. the fotolumen sign with our fotolumen user names. so fotolumen logo and next to it. @ravelquintos81 @borneta557 then the following hashtags: #vuelopardo #tiotraecafetitos #guardianesdelmaizdorado #torneo2019
3. If you can add the Telarista Logo (which is a channel logo) somewhere so it grabs attention from media it would be cool. Not mandatory.
4. Logo of mexican national team (this can take a lot of space)
5. Lastly the main text or content which would take most of the space, 'Vamos México, vamos Selección! Contigo siempre de corazón!
IF YOU ARE ABLE TO USE MOST PICTURES AND MAKE IT LOOK NICE AND THAT IT FLOWS YOULL MAKE MY LIFE.
Updates
i made a small change with main text. I really like the mexican national logo as back ground even if i have to lose out on the crappy pixilated images. LIke I've said before u can find better images online. fotolumen logo on bottom is important with first user names @ravelquintos81 @borneta557 followed by all the hashtags
Sorry guys i screwed up the size is not 8 by 10 but 3 feet by 8 feet! I am sorry, I will add additional prize amount for the troubles! I will add additional $30 dollars

```html
<!DOCTYPE html>
<html lang="es">
<head>
<meta charset="utf-8">
<title>Vamos México – banner</title>
<link rel="stylesheet" href="https://fonts.googleapis.com/css2?family=Rubik+Dirt&family=Baloo+2:wght@800&display=swap">
<style>
  :root {
    --page: #ffffff;
    --green-deep: #0f3a1c;
    --green: #1f6b35;
    --stone: #d9d4cc;
    --stone-dark: #a9a196;
    --red: #c0321c;
    --red-deep: #6e1208;
    --text: #ffffff;
    --crest: #8a7a5c;
    --saint-frame: #e9dcae;
    --saint-light: #e6d6a4;
    --saint-robe: #7d6a45;
    --fotolumen: #b9723f;
  }
  * { margin: 0; padding: 0; box-sizing: border-box; }
  html, body { width: 1200px; height: 900px; overflow: hidden; background: var(--page); }
  .canvas { position: relative; width: 1200px; height: 900px; }
  .banner { position: absolute; left: 28px; top: 262px; width: 1130px; height: 423px; overflow: hidden; }
  .banner-bg { position: absolute; inset: 0; }
  .channel-mark { position: absolute; left: 18px; top: 14px; display: flex; flex-direction: column; align-items: center; gap: 4px; }
  .channel-dot { width: 34px; height: 34px; border-radius: 50%; background: var(--text); opacity: .85; }
  .channel-name { font-family: "Baloo 2", sans-serif; font-weight: 800; font-size: 12px; letter-spacing: 1px; color: var(--text); text-transform: uppercase; }
  .headline { position: absolute; left: 0; right: 0; text-align: center; font-family: "Rubik Dirt", sans-serif; font-weight: 400; font-size: 56px; line-height: 83px; letter-spacing: 1px; color: var(--text); text-transform: uppercase; text-shadow: 3px 4px 6px rgba(0,0,0,.55); }
  .headline-1 { top: 32px; }
  .headline-2 { top: 219px; }
  .headline span { display: block; }
  .social { position: absolute; left: 20px; top: 340px; display: flex; align-items: center; gap: 10px; }
  .social-brand { display: flex; flex-direction: column; align-items: center; gap: 2px; }
  .social-square { width: 54px; height: 54px; border-radius: 10px; background: var(--fotolumen); }
  .social-name { font-family: "Baloo 2", sans-serif; font-weight: 800; font-size: 9px; color: var(--text); text-transform: uppercase; }
  .handles { font-family: "Baloo 2", sans-serif; font-weight: 800; font-size: 22px; line-height: 1.2; color: var(--text); text-transform: uppercase; text-shadow: 1px 2px 3px rgba(0,0,0,.5); }
  .hashtags { position: absolute; right: 22px; top: 306px; text-align: right; font-family: "Baloo 2", sans-serif; font-weight: 800; font-size: 17px; line-height: 22px; color: var(--text); text-transform: uppercase; text-shadow: 1px 2px 3px rgba(0,0,0,.5); }
</style>
</head>
<body>
<div class="canvas">
  <section class="banner">
    <svg class="banner-bg" width="1130" height="423" viewBox="0 0 1130 423">
      <defs>
        <linearGradient id="flag" x1="0" x2="1" y1="0" y2="0">
          <stop offset="0" stop-color="var(--green-deep)"/>
          <stop offset="0.28" stop-color="var(--green)"/>
          <stop offset="0.34" stop-color="var(--stone-dark)"/>
          <stop offset="0.4" stop-color="var(--stone)"/>
          <stop offset="0.62" stop-color="var(--stone)"/>
          <stop offset="0.69" stop-color="var(--stone-dark)"/>
          <stop offset="0.74" stop-color="var(--red)"/>
          <stop offset="1" stop-color="var(--red-deep)"/>
        </linearGradient>
        <radialGradient id="vignette" cx="0.5" cy="0.5" r="0.75">
          <stop offset="0.55" stop-color="#000" stop-opacity="0"/>
          <stop offset="1" stop-color="#000" stop-opacity="0.45"/>
        </radialGradient>
        <radialGradient id="crestFill" cx="0.5" cy="0.45" r="0.55">
          <stop offset="0" stop-color="var(--crest)" stop-opacity="0.7"/>
          <stop offset="1" stop-color="var(--crest)" stop-opacity="0.2"/>
        </radialGradient>
        <radialGradient id="saintFill" cx="0.5" cy="0.35" r="0.7">
          <stop offset="0" stop-color="var(--saint-light)"/>
          <stop offset="1" stop-color="var(--saint-robe)"/>
        </radialGradient>
      </defs>
      <rect width="1130" height="423" fill="url(#flag)"/>
      <rect width="1130" height="423" fill="url(#vignette)"/>
      <ellipse cx="570" cy="230" rx="160" ry="190" fill="url(#crestFill)" role="img" aria-label="Crest of the national football team"/>
      <ellipse cx="182" cy="168" rx="96" ry="146" fill="var(--saint-frame)"/>
      <ellipse cx="182" cy="168" rx="87" ry="137" fill="url(#saintFill)" role="img" aria-label="Saint holding a child, devotional portrait"/>
      <ellipse cx="934" cy="168" rx="96" ry="146" fill="var(--saint-frame)"/>
      <ellipse cx="934" cy="168" rx="87" ry="137" fill="url(#saintFill)" role="img" aria-label="Saint holding a medallion, devotional portrait"/>
    </svg>

    <div class="channel-mark">
      <div class="channel-dot"></div>
      <div class="channel-name">Telarista</div>
    </div>

    <h1 class="headline headline-1"><span>Vamos México,</span><span>Vamos Selección!</span></h1>
    <h2 class="headline headline-2"><span>Contigo siempre</span><span>de corazon!</span></h2>

    <div class="social">
      <div class="social-brand">
        <div class="social-square"></div>
        <div class="social-name">Fotolumen</div>
      </div>
      <div class="handles">
        <div>@ravelquintos81</div>
        <div>@borneta557</div>
      </div>
    </div>

    <div class="hashtags">
      <div>#vuelopardo</div>
      <div>#torneo2019</div>
      <div>#tiotraecafetitos</div>
      <div>#guardianesdelmaizdorado</div>
      <div>#procurandoumanamoradabrasileira</div>
    </div>
  </section>
</div>
</body>
</html>
```